Silver Kite Venture Series Travel Brochure

I'm looking for a brochure design for a new travel product - Silver Kite Venture Series, catering for students above 12 years old. Target audience are schools that do destination projects. Brochure to be read by head teacher, parents and students.

Brochure should be A4 in size, 4-6 pages. Format of brochure is hard cover (a folder) with inlet for flyers. Flyers for destinations will be updated from time to time.

Finished job needs to be converted to electronic format for website and email proposal usage.

Attached is text to be used on brochure. Order of section can be adjusted.

For "Elements of the trip", please understand the contents and explain/display it in a graphic form.

For flyer, please come out with a template that I can use for other destinations. The main elements - what's included, number of days, location for pictures, itinerary, educational focus, should be alterable. Attached are text for two sample destinations.
Also attached (tour itinerary example) a version of flyer that I like.

I'm attaching some pictures here. If you find more suitable pictures, please feel free to use them.

Reason: I'm extending the deadline of this project by 4 days, as I need to add details & photo of another travel specialist in personnel session (total of 3 members). Also, in view of the amount of work a designer has to do for this project, I'm giving you more time for submission. Please do not hesitate to be in touch should you need more than 4 days extension. Thank you.

Target Market(s)

Schools - especially the head teacher and parents, to send students above 12 years old to travel

Industry/Entity Type

Electronic

Requirements
Must have
• This is a travel brochure with education elements in it. Parents feel better when their children are travelling for a purpose and lead by responsible teachers/adults whom they can trust. So, the design has to emphasis that education elements and safety are our utmost priority.
Nice to have
• We specialise in environmental study. So, it is nice to have the environmental touch in the design.
Should not have
• Our target market segment is the Middle East, which can be quite sensitive to religion. I prefer not to have any religious related illustration on the design.

```html
<!DOCTYPE html>
<html lang="en">
<head>
<meta charset="utf-8">
<title>Silver Kite Venture Series – Destination 3 Egypt</title>
<link rel="stylesheet" href="https://fonts.googleapis.com/css2?family=Alfa+Slab+One&family=Lato:wght@300;400;700&family=Open+Sans:ital,wght@1,700&family=PT+Sans:ital,wght@0,400;0,700;1,400&display=swap">
<style>
:root{
  --ink:#1d2733;
  --brand-blue:#2f6fb8;
  --sky-blue:#3f8fd2;
  --pale-blue:#a9cdee;
  --navy:#173d70;
  --leaf:#8cc63f;
  --leaf-mid:#7bb833;
  --leaf-dark:#5f9b22;
  --paper:#ffffff;
  --canvas:#f3f3f3;
  --edge:#c9c9c9;
}
*{box-sizing:border-box;margin:0;padding:0}
html,body{width:949px;height:1200px;overflow:hidden;background:var(--canvas)}
body{font-family:"PT Sans",Arial,sans-serif;color:var(--ink)}
.spread{position:relative;width:949px;height:1200px}
.page{position:absolute;width:385px;height:551px;background:var(--paper);border:1px solid var(--edge);overflow:hidden}
.page--1{left:26px;top:24px}
.page--3{left:485px;top:24px}
.page--2{left:26px;top:602px}
.page--4{left:485px;top:602px}
.page-number{position:absolute;font:300 30px "Lato",sans-serif;color:#222}

/* brand */
.brand{position:absolute;display:flex;align-items:center;gap:4px;font:700 11px "Lato",sans-serif;color:var(--brand-blue)}
.brand-mark{width:9px;height:9px;background:var(--brand-blue)}
.series-title{position:absolute;left:96px;top:20px;font:400 17px "Lato",sans-serif;color:var(--brand-blue)}

/* cover */
.cover-photo{position:absolute;left:0;top:58px;width:222px;height:340px;background:linear-gradient(180deg,#6f9fd4 0%,#a9c1d8 38%,#c8a978 62%,#8a6a45 100%)}
.cover-panel{position:absolute;left:216px;top:82px;width:169px;height:316px;background:var(--leaf)}
.cover-leaf{position:absolute;left:140px;top:66px;width:245px;height:38px;background:var(--leaf-mid)}
.destination{position:absolute;left:48px;top:258px;color:#fff}
.destination-label{font:700 13px "PT Sans",sans-serif}
.destination-name{font:400 34px/1 "Alfa Slab One",serif;letter-spacing:1px}
.itinerary{position:absolute;left:224px;top:112px;width:156px;list-style:none}
.itinerary li{font:400 7.6px/9px "PT Sans",sans-serif;color:var(--ink);margin-bottom:2px}
.itinerary b{display:block;color:#fff;font:700 8.4px/10px "PT Sans",sans-serif}
.focus-box{position:absolute;left:0;top:398px;width:206px;height:153px;background:var(--navy);padding:12px 12px 0 12px;color:#fff}
.focus-box h3{font:700 11px/12px "PT Sans",sans-serif;color:var(--leaf)}
.focus-box p{font:700 9px/10.5px "PT Sans",sans-serif;margin-bottom:6px}
.included{position:absolute;left:220px;top:405px;width:160px}
.included h3{font:700 10.5px "PT Sans",sans-serif;color:var(--leaf-dark);margin-bottom:5px}
.included ul{list-style:none}
.included li{display:flex;align-items:center;gap:7px;font:400 8px/9px "PT Sans",sans-serif;height:20px}
.included svg{width:20px;height:14px;flex:none}

/* day blocks */
.band{position:absolute;left:0;width:385px;background:var(--sky-blue)}
.band--pale{background:var(--pale-blue)}
.day-tab{position:absolute;width:74px;height:18px;background:var(--leaf);border-radius:3px;font:700 italic 11px/18px "Open Sans",sans-serif;color:#fff;text-align:center}
.meals{position:absolute;display:flex;align-items:center;gap:3px;font:700 8.5px "PT Sans",sans-serif;color:var(--navy)}
.meals--light{color:#fff}
.meals svg{width:11px;height:9px}
.photo{position:absolute;overflow:hidden}
.photo-caption{position:absolute;left:0;bottom:0;width:100%;padding:3px 5px;background:rgba(15,43,82,.85);font:700 8.5px "PT Sans",sans-serif;color:#fff}
.photo--giza{background:linear-gradient(180deg,#9bb9da,#c9a879 60%,#8c7150)}
.photo--museum{background:linear-gradient(160deg,#6a4a2a,#c99a55 50%,#3c2a1c)}
.photo--aswan{background:linear-gradient(180deg,#7aa7d6,#d8cbb0 55%,#6f8c9a)}
.photo--cruise{background:linear-gradient(180deg,#d9b77a,#a77b45 60%,#5f4426)}
.photo--luxor{background:linear-gradient(180deg,#86aedb,#c6a26c 55%,#7e5d3a)}
.photo--tomb{background:linear-gradient(160deg,#c89b5c,#e2c99b 50%,#8c6a42)}
.photo--sunset{background:linear-gradient(180deg,#e6a04a,#b96b2a 55%,#3a2a1e)}
.copy{position:absolute;column-count:2;column-gap:9px;font:400 5.5px/6.8px "PT Sans",sans-serif;color:var(--ink)}
.copy--light{color:#fff}
.copy p{margin-bottom:2.5px;break-inside:avoid}
.copy h4{font:700 6.6px/7.6px "PT Sans",sans-serif;color:var(--navy);break-after:avoid}
.copy--light h4{color:#fff}
.copy--single{column-count:1}
.departure{position:absolute;left:279px;top:146px;width:106px;height:38px;background:var(--navy);color:#fff;font:700 9px "PT Sans",sans-serif;display:flex;align-items:flex-end;padding:0 0 5px 8px}

/* back page */
.closing{position:absolute;left:22px;top:264px;width:341px;text-align:center;font:400 12.5px/16.5px "Lato",sans-serif;color:var(--brand-blue)}
.contact{position:absolute;left:14px;font:400 5.6px/7px "PT Sans",sans-serif;color:var(--ink)}
.contact b{font-weight:700}
.icon-row{position:absolute;left:206px;top:520px;display:flex;gap:6px}
.icon-row svg{width:22px;height:15px}
</style>
</head>
<body>
<svg width="0" height="0" style="position:absolute" aria-hidden="true">
  <defs>
    <symbol id="icon-ticket" viewBox="0 0 22 14"><rect x="1" y="2" width="20" height="10" rx="1" fill="#1d2733"/><rect x="4" y="6" width="11" height="2" fill="#fff"/><path d="M17 5l3 2-3 2z" fill="#fff"/></symbol>
    <symbol id="icon-bed" viewBox="0 0 22 14"><rect x="1" y="3" width="2" height="10" fill="#1d2733"/><rect x="1" y="8" width="20" height="3" fill="#1d2733"/><rect x="19" y="8" width="2" height="5" fill="#1d2733"/><circle cx="6" cy="6" r="2" fill="#1d2733"/><rect x="9" y="5" width="11" height="3" rx="1" fill="#1d2733"/></symbol>
    <symbol id="icon-director" viewBox="0 0 22 14"><circle cx="11" cy="3" r="2.4" fill="#1d2733"/><path d="M7 13l1.5-7h5L15 13z" fill="#1d2733"/></symbol>
    <symbol id="icon-meal" viewBox="0 0 22 14"><circle cx="11" cy="7" r="5.5" fill="none" stroke="#1d2733" stroke-width="1.6"/><rect x="3" y="1" width="1.4" height="12" fill="#1d2733"/><rect x="17.6" y="1" width="1.4" height="12" fill="#1d2733"/></symbol>
    <symbol id="icon-guide" viewBox="0 0 22 14"><circle cx="7" cy="4" r="2" fill="#1d2733"/><path d="M4 13l1.5-6h3L10 13z" fill="#1d2733"/><circle cx="14" cy="5" r="1.8" fill="#5f9b22"/><path d="M11.5 13l1.3-5.5h2.4L16.5 13z" fill="#5f9b22"/><rect x="18" y="1" width="1" height="12" fill="#1d2733"/><path d="M19 1h3l-1 2 1 2h-3z" fill="#5f9b22"/></symbol>
    <symbol id="icon-entry" viewBox="0 0 22 14"><rect x="1" y="2" width="20" height="10" rx="2" fill="#5f9b22"/><rect x="5" y="6" width="12" height="2" fill="#1d2733"/></symbol>
    <symbol id="icon-plate" viewBox="0 0 11 9"><circle cx="5.5" cy="4.5" r="3.3" fill="currentColor"/><rect x="0.3" y="0.5" width="0.9" height="8" fill="currentColor"/><rect x="9.8" y="0.5" width="0.9" height="8" fill="currentColor"/></symbol>
  </defs>
</svg>

<main class="spread">

  <!-- Cover -->
  <section class="page page--1">
    <div class="brand" style="left:20px;top:24px"><span class="brand-mark"></span>Harbourline</div>
    <h1 class="series-title">Silver Kite Venture Series</h1>
    <div class="cover-photo" role="img" aria-label="Photo of the Giza pyramids under a blue sky"></div>
    <div class="cover-panel"></div>
    <div class="cover-leaf" role="img" aria-label="Green leaf illustration across the top of the cover"></div>
    <div class="destination">
      <div class="destination-label">Destination 3</div>
      <div class="destination-name">EGYPT</div>
    </div>
    <ul class="itinerary">
      <li><b>Day 1</b>Arrival at Cairo – Cairo city tour – Pyramid and Sphinx</li>
      <li><b>Day 2</b>Cairo Museum &amp; Khan El Khalili Bazaar – Cairo to Aswan by flight or train</li>
      <li><b>Day 3</b>Embark on Nile Cruise – Visit high dam, unfinished obelisk, Philae Temple</li>
      <li><b>Day 4</b>Nile Cruise: visit Temple of Kom Ombo and Edfu Temple</li>
      <li><b>Day 5</b>Nile Cruise: visit Temple of Karnak and Temple of Luxor</li>
      <li><b>Day 6</b>Disembark from Nile Cruise – visit Luxor – Colossi of Memnon – Valley of the Kings and Hatshepsut Temple</li>
      <li><b>Day 7</b>Luxor visit Colossi of Memnon – Valley of the King – Hatshepsut Temple – Luxor to Cairo by train</li>
      <li><b>Day 8</b>Departure</li>
    </ul>
    <div class="focus-box">
      <h3>Main focus subject</h3>
      <p>History and Anthropology</p>
      <h3>Related subjects</h3>
      <p>Geography<br>Development Studies<br>Agriculture<br>Environmental Management</p>
      <h3>Environmental focus</h3>
      <p>Impact of climate change on the<br>Nile river basin.</p>
    </div>
    <div class="included">
      <h3>What's included in price:</h3>
      <ul>
        <li><svg><use href="#icon-ticket"/></svg>Air ticket</li>
        <li><svg><use href="#icon-bed"/></svg>All accommodation</li>
        <li><svg><use href="#icon-director"/></svg>Full time tour director</li>
        <li><svg><use href="#icon-meal"/></svg>Meals</li>
        <li><svg><use href="#icon-guide"/></svg>Tours led by local<br>expert tour guides</li>
        <li><svg><use href="#icon-entry"/></svg>Entrance fees to<br>attractions</li>
      </ul>
    </div>
  </section>
  <span class="page-number" style="left:422px;top:530px">1</span>

  <!-- Days 1–3 -->
  <section class="page page--2">
    <div class="photo photo--giza" style="left:0;top:42px;width:118px;height:160px" role="img" aria-label="Photo of the step pyramid near Cairo"><span class="photo-caption">Arrival at Cairo</span></div>
    <div class="day-tab" style="left:128px;top:38px">Day 1</div>
    <div class="meals" style="right:12px;top:42px"><svg><use href="#icon-plate"/></svg>L/D</div>
    <div class="copy" style="left:126px;top:62px;width:252px;height:140px">
      <p>Welcome to historical Egypt! Upon arrival at Cairo Airport, you will be met and escorted through passport control. You will then travel to Giza to see the famous Sphinx and visit the Great Pyramids, built as tombs for ancient kings. Each pyramid once stood inside a wide funeral complex with temples and causeways.</p>
      <p>After lunch, visit the Step Pyramid of Djoser, the oldest stone building in Egypt, and learn how its builders worked.</p>
      <p>Overnight in Cairo.</p>
    </div>

    <div class="band" style="top:210px;height:100px"></div>
    <div class="day-tab" style="left:222px;top:206px">Day 2</div>
    <div class="meals meals--light" style="left:10px;top:216px"><svg><use href="#icon-plate"/></svg>B/D</div>
    <div class="copy copy--light" style="left:10px;top:232px;width:246px;height:74px">
      <p>After breakfast, you will take a tour of the world famous Egyptian Museum, home to thousands of objects from ancient Egyptian life. You will then browse the old souk of Khan El Khalili Bazaar.</p>
      <p>In the evening, take a transfer to the station for the overnight sleeper train to Aswan.</p>
    </div>
    <div class="photo photo--museum" style="left:262px;top:224px;width:123px;height:86px" role="img" aria-label="Photo of a lantern-lit street in the Cairo bazaar"><span class="photo-caption">Cairo Museum &amp;<br>Bazaar</span></div>

    <div class="photo photo--aswan" style="left:0;top:318px;width:118px;height:162px" role="img" aria-label="Photo of Philae Temple beside the Nile at Aswan"><span class="photo-caption">Aswan – Nile Cruise</span></div>
    <div class="day-tab" style="left:128px;top:314px">Day 3</div>
    <div class="meals" style="right:12px;top:318px"><svg><use href="#icon-plate"/></svg>B/L/D</div>
    <div class="copy" style="left:126px;top:338px;width:252px;height:142px">
      <p>Upon arrival in Aswan, you will be transferred to the Nile Cruise and welcomed on board. Sit back and relax for your tour of Aswan.</p>
      <h4>High dam</h4>
      <p>The high dam is the largest rock-filled dam in the world and one of the key engineering works of the last century.</p>
      <h4>Unfinished obelisk</h4>
      <p>This huge obelisk still lies in the quarry where it cracked during carving.</p>
      <h4>Philae Temple</h4>
      <p>Moved stone by stone to a nearby island when the dam raised the river.</p>
      <p>Overnight on cruise.</p>
    </div>

    <p class="contact" style="top:494px"><b>Harbourline Travel Management</b><br>Suite 402 Cedar Point Offices, Marina Row<br>PO Box 10442, Dubai, UAE<br><b>Tel:</b> +971 4 000 1111<br><b>Fax:</b> +971 4 000 1112<br><b>Email:</b> hello@harbourline-travel.example</p>
  </section>
  <span class="page-number" style="left:422px;top:1108px">2</span>

  <!-- Days 4–6 -->
  <section class="page page--3">
    <div class="band" style="top:42px;height:22px"></div>
    <div class="day-tab" style="left:270px;top:36px">Day 4</div>
    <div class="meals meals--light" style="left:10px;top:48px">B/L/D<svg><use href="#icon-plate"/></svg></div>
    <div class="copy" style="left:8px;top:70px;width:242px;height:140px">
      <p>Breakfast on board. You will sail towards Kom Ombo and Edfu.</p>
      <h4>Temple of Kom Ombo</h4>
      <p>This unusual double temple was built for two gods, so every hall and gate is doubled from end to end.</p>
      <h4>Edfu Temple</h4>
      <p>One of the best preserved temples in Egypt, with tall gates and carved walls.</p>
      <p>Continue sailing to Luxor. Overnight on cruise.</p>
    </div>
    <div class="photo photo--cruise" style="left:256px;top:64px;width:129px;height:150px" role="img" aria-label="Photo of a carved temple gateway seen from the Nile Cruise"><span class="photo-caption" style="text-align:right">Nile Cruise</span></div>

    <div class="photo photo--luxor" style="left:0;top:222px;width:120px;height:132px" role="img" aria-label="Photo of seated stone statues at Luxor"><span class="photo-caption">Nile Cruise – Luxor</span></div>
    <div class="day-tab" style="left:122px;top:218px">Day 5</div>
    <div class="meals" style="left:220px;top:222px"><svg><use href="#icon-plate"/></svg>B/L/D</div>
    <div class="copy" style="left:128px;top:244px;width:250px;height:110px">
      <p>Today you will be cruising into Luxor. Upon arrival, you will be taken to visit the impressive temples of Karnak and Luxor.</p>
      <h4>Temple of Karnak</h4>
      <p>It is the largest temple complex in the world, built and enlarged over many centuries.</p>
      <h4>Temple of Luxor</h4>
      <p>It is close to the Nile and was linked to Karnak by a long avenue of sphinxes.</p>
      <p>Overnight on cruise.</p>
    </div>

    <div class="band" style="top:362px;height:18px"></div>
    <div class="band band--pale" style="top:380px;height:142px"></div>
    <div class="day-tab" style="left:270px;top:354px">Day 6</div>
    <div class="meals meals--light" style="left:10px;top:366px">B/D<svg><use href="#icon-plate"/></svg></div>
    <div class="copy" style="left:8px;top:386px;width:238px;height:132px">
      <p>After breakfast, you will disembark from the Nile Cruise and then visit the west bank.</p>
      <h4>Colossi of Memnon</h4>
      <p>Two huge stone statues that have guarded the plain for over three thousand years.</p>
      <h4>Valley of the Kings</h4>
      <p>A valley of rock-cut tombs where the rulers of the New Kingdom were laid to rest.</p>
      <h4>Hatshepsut Temple</h4>
      <p>A terraced temple set against tall cliffs.</p>
      <p>Transfer to Luxor station for the sleeper train to Cairo. Overnight on train.</p>
    </div>
    <div class="photo photo--tomb" style="left:252px;top:380px;width:133px;height:142px" role="img" aria-label="Photo of painted wall reliefs in a Luxor tomb"><span class="photo-caption" style="text-align:right">Luxor – Cairo</span></div>
  </section>
  <span class="page-number" style="left:898px;top:530px">3</span>

  <!-- Days 7–8 and back page -->
  <section class="page page--4">
    <div class="photo photo--sunset" style="left:0;top:54px;width:128px;height:84px" role="img" aria-label="Photo of the Cairo skyline at sunset over the Nile"><span class="photo-caption" style="background:none">Cairo</span></div>
    <div class="day-tab" style="left:136px;top:52px">Day 7</div>
    <div class="meals" style="right:14px;top:56px"><svg><use href="#icon-plate"/></svg>B</div>
    <div class="copy copy--single" style="left:138px;top:76px;width:200px;height:56px">
      <p>Breakfast at hotel. Today is your free day to wander around Cairo. You may also choose to visit local markets and gardens at your own pace.</p>
    </div>

    <div class="band" style="top:146px;height:24px;width:140px"></div>
    <div class="day-tab" style="left:136px;top:144px">Day 8</div>
    <div class="meals meals--light" style="left:10px;top:152px">B<svg><use href="#icon-plate"/></svg></div>
    <div class="departure">Departure</div>
    <div class="copy copy--single" style="left:138px;top:174px;width:136px;height:20px">
      <p>After breakfast, free and easy until time to transfer to the airport for departure.</p>
    </div>

    <p class="closing">It is only one of our more popular destinations. With our vast knowledge and expertise in the Middle East, Asia and Europe destinations, we are able to cater for other countries not mentioned. We are constantly expanding our radar to new destinations. Upcoming destinations are Vietnam, Cambodia and Namibia.</p>

    <div class="brand" style="left:14px;top:476px"><span class="brand-mark"></span>Harbourline</div>
    <p class="contact" style="top:496px"><b>Harbourline Travel Management</b><br>Suite 402 Cedar Point Offices, Marina Row<br>PO Box 10442, Dubai, UAE<br><b>Tel:</b> +971 4 000 1111<br><b>Fax:</b> +971 4 000 1112<br><b>Email:</b> hello@harbourline-travel.example</p>
    <div class="icon-row" aria-hidden="true">
      <svg><use href="#icon-ticket"/></svg>
      <svg><use href="#icon-bed"/></svg>
      <svg><use href="#icon-director"/></svg>
      <svg><use href="#icon-meal"/></svg>
      <svg><use href="#icon-guide"/></svg>
      <svg><use href="#icon-entry"/></svg>
    </div>
  </section>
  <span class="page-number" style="left:898px;top:1108px">4</span>

</main>
</body>
</html>
```